Copper Lantern

Need a business card for our restaurant. Restaurant and Bar in the mountains of North Idaho. Rustic looking card

rustic design, wood and metal looking, primarily neutral colors

• Name, address, phone number, website, email address

```html
<!DOCTYPE html>
<html lang="en">
<head>
<meta charset="utf-8">
<title>Copper Lantern – Business Card</title>
<link rel="stylesheet" href="https://fonts.googleapis.com/css2?family=Montserrat:wght@400;700&display=swap">
<style>
  :root {
    --stage: #2a2a2a;
    --card: #1b1b1b;
    --ink: #f4f4f4;
    --gloss: #343434;
    --gloss-edge: #3d3d3d;
  }
  * { margin: 0; padding: 0; box-sizing: border-box; }
  html, body {
    width: 1200px; height: 875px; overflow: hidden;
    background: var(--stage);
    font-family: "Montserrat", sans-serif;
  }
  .sheet {
    width: 1200px; height: 875px;
    display: flex; align-items: center; justify-content: center; gap: 40px;
  }
  .card {
    position: relative;
    width: 540px; height: 310px;
    background: var(--card);
    border-radius: 18px;
    overflow: hidden;
  }

  /* back face: glossy mark */
  .card-back { display: flex; align-items: center; justify-content: center; }
  .gloss-mark {
    display: flex; align-items: center; gap: 14px;
    color: var(--gloss);
  }
  .gloss-mark .dot {
    width: 34px; height: 34px; border-radius: 50%;
    border: 3px solid var(--gloss-edge);
  }
  .gloss-mark .name {
    font-weight: 700; font-size: 34px; letter-spacing: 0.08em; text-transform: uppercase;
    color: var(--gloss);
  }

  /* front face: contact */
  .card-front {
    display: flex; align-items: center;
    padding: 0 0 0 48px;
  }
  .brand {
    width: 200px; display: flex; flex-direction: column; align-items: center; gap: 12px;
    color: var(--ink);
  }
  .brand .dot {
    width: 26px; height: 26px; border-radius: 50%;
    border: 3px solid var(--ink);
  }
  .brand .name {
    font-weight: 700; font-size: 22px; letter-spacing: 0.08em; text-transform: uppercase;
    text-align: center; line-height: 1.2;
  }
  .divider {
    width: 2px; height: 190px; background: var(--ink);
    margin: 0 22px 0 24px;
  }
  .contact { color: var(--ink); }
  .contact .person { font-weight: 700; font-size: 24px; line-height: 1.1; }
  .contact .role { font-size: 13px; margin: 4px 0 16px; }
  .contact .address { font-size: 13px; line-height: 1.35; margin-bottom: 14px; }
  .contact ul { list-style: none; font-size: 13px; }
  .contact li { display: flex; align-items: center; gap: 9px; line-height: 1.75; }
  .contact svg { width: 12px; height: 12px; fill: var(--ink); flex: none; }
</style>
</head>
<body>
<main class="sheet">

  <section class="card card-back" aria-label="Card back">
    <div class="gloss-mark">
      <span class="dot"></span>
      <span class="name">Copper Lantern</span>
    </div>
  </section>

  <section class="card card-front" aria-label="Card front">
    <div class="brand">
      <span class="dot"></span>
      <span class="name">Copper<br>Lantern</span>
    </div>
    <div class="divider"></div>
    <div class="contact">
      <p class="person">Evan Hale</p>
      <p class="role">Managing Director</p>
      <p class="address">48 Cedar Ridge Road,<br>Pine Hollow, USA</p>
      <ul>
        <li>
          <svg viewBox="0 0 16 16"><path d="M3 1h3l1.5 4-2 1.2a9 9 0 0 0 4.3 4.3L11 8.5l4 1.5v3a2 2 0 0 1-2 2A12 12 0 0 1 1 3a2 2 0 0 1 2-2z"/></svg>
          (08) 4410 2276
        </li>
        <li>
          <svg viewBox="0 0 16 16"><path d="M1 3h14v10H1z M1 3l7 6 7-6" fill="none" stroke="#f4f4f4" stroke-width="1.6"/></svg>
          hello@copperlantern.com
        </li>
        <li>
          <svg viewBox="0 0 16 16"><circle cx="8" cy="8" r="6.5" fill="none" stroke="#f4f4f4" stroke-width="1.5"/><path d="M1.5 8h13M8 1.5c-3 3.5-3 9.5 0 13M8 1.5c3 3.5 3 9.5 0 13" fill="none" stroke="#f4f4f4" stroke-width="1.2"/></svg>
          www.copperlantern.com
        </li>
      </ul>
    </div>
  </section>

</main>
</body>
</html>
```